Fresh, modern, fun business card for pediatric dental practice

Need a business card for fresh, modern, fun pediatric dental practice

Clean look that matches our website's font and colors

We prefer the look of curved corners on business cards

Target Market(s)

parents (mothers) of young children, professionals, mid-high class

Industry/Entity Type

Dental

Contact Information for Business Card

Maplebrook Pediatric Dentistry
482 Quarry Lane
Suite 517
Larkfield, VT 05999
555.555.0193
www.maplebrookkidsdental.example

Mei-Ran Tsai, DMD
Corinne Walbeck, DMD
(we are working on our email address, but we would like that on the card as well)

Font styles to use
Sans Serif

Requirements
Must have
• All info; we would also like to make cards for individual staff members
• colors from our website and color palatte, attatched
• use same font and design as website for branding
Nice to have
• clean, simple card that has a pop of color
• we would like to see a few designs with our tag line "where smiles get brighter"
• we are not sure if we want to have it on there or not
• we would like to see a few designs incorporating the ribbon graphic on our website where the word WELCOME is

```html
<!DOCTYPE html>
<html lang="en">
<head>
<meta charset="utf-8">
<title>Maplebrook Pediatric Dentistry – Business Card</title>
<link rel="stylesheet" href="https://fonts.googleapis.com/css2?family=Lato:wght@400;700&display=swap">
<style>
  :root {
    --backdrop: #1c1a1b;
    --card-white: #ffffff;
    --card-plum: #461f42;
    --gold: #f2b01e;
    --magenta: #d4318c;
    --ink: #454545;
    --light: #f4f1f3;
  }
  * { margin: 0; padding: 0; box-sizing: border-box; }
  html, body { width: 1200px; height: 897px; overflow: hidden; }
  body {
    background: var(--backdrop);
    font-family: "Lato", sans-serif;
    position: relative;
  }
  .card {
    position: absolute;
    left: 303px;
    width: 595px;
    height: 338px;
    border-radius: 22px;
    overflow: hidden;
  }
  .card--front { top: 92px; background: var(--card-white); }
  .card--back  { top: 470px; background: var(--card-plum); }

  .brand {
    position: absolute;
    text-align: center;
    color: var(--gold);
    font-weight: 700;
  }
  .brand__dot {
    display: block;
    margin: 0 auto 10px;
    border-radius: 50%;
    background: var(--gold);
  }
  .brand__name { display: block; line-height: 1; }
  .brand__sub { display: block; line-height: 1.2; letter-spacing: 1.5px; }

  .card--front .brand { left: 30px; width: 264px; top: 120px; }
  .card--front .brand__dot { width: 34px; height: 34px; }
  .card--front .brand__name { font-size: 36px; }
  .card--front .brand__sub { font-size: 16px; margin-top: 6px; }

  .card--back .brand { left: 0; width: 100%; top: 100px; }
  .card--back .brand__dot { width: 46px; height: 46px; margin-bottom: 14px; }
  .card--back .brand__name { font-size: 52px; }
  .card--back .brand__sub { font-size: 22px; margin-top: 8px; letter-spacing: 2px; }

  .divider {
    position: absolute;
    left: 297px;
    top: 90px;
    width: 2px;
    height: 160px;
    background: var(--magenta);
  }
  .details {
    position: absolute;
    left: 325px;
    top: 86px;
    color: var(--ink);
    font-size: 14px;
    line-height: 18px;
  }
  .details__name {
    color: var(--gold);
    font-size: 20px;
    font-weight: 700;
    letter-spacing: 0.6px;
    line-height: 24px;
  }
  .details__title { font-size: 15px; margin-bottom: 8px; }
  .details__practice { color: var(--gold); font-weight: 700; }
  .contact { list-style: none; margin-top: 8px; }
  .contact li { display: flex; align-items: center; gap: 10px; height: 19px; white-space: nowrap; }
  .contact svg { width: 12px; height: 12px; flex: none; }

  .web {
    position: absolute;
    left: 0;
    width: 100%;
    top: 292px;
    text-align: center;
    color: var(--light);
    font-size: 15px;
    letter-spacing: 1.3px;
  }
  .web__domain { color: var(--gold); }
</style>
</head>
<body>
  <section class="card card--front" aria-label="Business card front">
    <div class="brand">
      <span class="brand__dot"></span>
      <span class="brand__name">maplebrook</span>
      <span class="brand__sub">pediatric dentistry</span>
    </div>
    <div class="divider"></div>
    <div class="details">
      <p class="details__name">CORINNE WALBECK</p>
      <p class="details__title">DMD</p>
      <p class="details__practice">Maplebrook Pediatric Dentistry</p>
      <p>482 Quarry Lane</p>
      <p>Suite 517 Larkfield, VT 05999</p>
      <ul class="contact">
        <li>
          <svg viewBox="0 0 12 12" aria-hidden="true"><path d="M2.4 1 4.3 3.2 3.3 4.6c.7 1.6 2.3 3.2 4 4l1.4-1L11 9.5 9.8 11C5.2 10.6 1.4 6.8 1 2.2Z" fill="var(--gold)"/></svg>
          555.555.0193
        </li>
        <li>
          <svg viewBox="0 0 12 12" aria-hidden="true"><rect x="1" y="2.5" width="10" height="7" fill="var(--gold)"/><path d="M1 2.5 6 6.5 11 2.5" fill="none" stroke="#fff" stroke-width="1"/></svg>
          info@maplebrookkidsdental.example
        </li>
        <li>
          <svg viewBox="0 0 12 12" aria-hidden="true"><g fill="none" stroke="var(--gold)" stroke-width="1"><circle cx="6" cy="6" r="5"/><ellipse cx="6" cy="6" rx="2.2" ry="5"/><path d="M1 6h10M2 3.5h8M2 8.5h8"/></g></svg>
          www.maplebrookkidsdental.example
        </li>
      </ul>
    </div>
  </section>

  <section class="card card--back" aria-label="Business card back">
    <div class="brand">
      <span class="brand__dot"></span>
      <span class="brand__name">maplebrook</span>
      <span class="brand__sub">pediatric dentistry</span>
    </div>
    <p class="web">www.<span class="web__domain">maplebrookkidsdental</span>.example</p>
  </section>
</body>
</html>
```